Letterhead Design for Law Firm

**Edit: I have added the photo of a bottom that I like.

------
We are looking for a re-design of our new letterhead. The letterhead is for a law firm and will be used for digital and traditionally printed correspondence.

Here are some suggestions:

- Please use colours are #8ec900 and simple black.
- Please do not use any type of "waves" at the bottom of the page. This is not in style at all.
- Please stay modern yet conservative.
- Please use font Segoe UI Light or similar if you can
- Avoid clipart or illustrations.
- Utilize ample white space in the layout so the design looks clean and information is easy to read at a glance. Don't overcrowd the letterhead.
- Make sure the letterhead design is consistent with our brand identity (see corvelith.ca)
-Please, no black headers or footers.

I am attaching my current letterhead and signature for your convenience.

Remember, the letterhead is an extension of our professional identity. We are a successful firm and trial lawyers who correspond with insurers, judges, lawyers, courts, clients, etc. Make it new, modern, attractive, yet powerful and conservative.

It needs to be easily printable. I would like the bleed removed in print so the black bar the bottom crosses the page (but the text is not near the edges)
Updates

Low design quality

Target Market(s)

Clients, Government Offices, Judiciary, Lawyers, Insurance Companies, Colleagues.

Industry/Entity Type

Law

Other font styles liked:
• Segoe UI LIght, Calibri Light,

Colors
00AB8E
00BBA5
67D7C9
C6EFE9
E9F9F6

Requirements
Must have
• Everything that is on the letterhead now.
Nice to have
• Cutting Edge design, yet conservative.
Should not have
• law firm cliche design, images,

```html
<!DOCTYPE html>
<html lang="en">
<head>
<meta charset="utf-8">
<title>Varenne Personal Injury Lawyers – Letterhead</title>
<link rel="stylesheet" href="https://fonts.googleapis.com/css2?family=Open+Sans:wght@300;400;600&display=swap">
<style>
  :root {
    --brand-green: #8ec900;
    --ink: #2b2b2b;
    --ink-soft: #3a3a3a;
    --rule-black: #000000;
    --paper: #ffffff;
    --backdrop: #e8e8e6;
    --signature-tone: #eef0ea;
  }
  * { margin: 0; padding: 0; box-sizing: border-box; }
  html, body {
    width: 1200px; height: 1141px; overflow: hidden;
    background: var(--backdrop);
    font-family: "Open Sans", sans-serif;
    color: var(--ink);
  }
  .letterhead {
    position: absolute; left: 211px; top: 20px;
    width: 779px; height: 1100px;
    background: var(--paper);
    font-weight: 300; font-size: 13px;
  }
  .side-band { position: absolute; left: 0; top: 0; width: 11px; height: 100%; background: var(--brand-green); }
  .foot-band { position: absolute; left: 0; bottom: 0; width: 100%; height: 11px; background: var(--rule-black); }
  .abs { position: absolute; }

  .firm-name {
    left: 53px; top: 34px;
    font-size: 60px; font-weight: 400; letter-spacing: 1px;
    color: var(--ink); line-height: 1;
  }

  .contact-block {
    left: 568px; top: 40px; width: 180px; height: 192px;
    border-left: 1px solid var(--brand-green);
    padding-left: 16px;
    font-size: 9.6px; font-weight: 400; line-height: 13px; color: var(--ink-soft);
  }
  .contact-row { display: flex; gap: 4px; align-items: flex-start; }
  .contact-row svg { flex: none; width: 8px; height: 8px; margin-top: 2.5px; fill: var(--brand-green); }
  .contact-row.spaced { margin-top: 4px; }
  .label { color: var(--brand-green); font-weight: 600; }
  .file-clerk { margin-top: 8px; }
  .practice { margin-top: 11px; }

  .line { font-size: 13px; line-height: 18.5px; }
  .heading { font-weight: 400; }

  .re-label { left: 53px; top: 509px; font-weight: 400; }
  .re-body { left: 221px; top: 509px; font-weight: 400; }

  .re-rule { left: 53px; top: 566px; width: 674px; height: 2px; background: var(--brand-green); }

  .signature-area {
    left: 53px; top: 846px; width: 210px; height: 56px;
    background: var(--signature-tone);
  }
</style>
</head>
<body>
<main class="letterhead">
  <div class="side-band"></div>

  <div class="abs firm-name">VARENNE</div>

  <aside class="abs contact-block">
    <div class="contact-row">
      <svg viewBox="0 0 10 10"><path d="M5 0a3.5 3.5 0 0 0-3.5 3.5C1.5 6 5 10 5 10s3.5-4 3.5-6.5A3.5 3.5 0 0 0 5 0zm0 5a1.5 1.5 0 1 1 0-3 1.5 1.5 0 0 1 0 3z"/></svg>
      <span>48 Harbour Street E., Suite 1210<br>Kingsford, ON&nbsp; K9R 2B6</span>
    </div>
    <div class="contact-row spaced">
      <svg viewBox="0 0 10 10"><path d="M0 4c0-2 2-3 5-3s5 1 5 3v1H7V4H3v1H0zM2 6h6l1 3H1z"/></svg>
      <span>555-210-4400</span>
    </div>
    <div class="contact-row">
      <svg viewBox="0 0 10 10"><path d="M2 0h5v3H2zM0 3h10v6H0zm2 2v1h2V5zm4 0v1h2V5z"/></svg>
      <span>555-210-4411</span>
    </div>
    <div class="contact-row">
      <svg viewBox="0 0 10 10"><path d="M0 2h10v1L5 6 0 3zm0 2l5 3 5-3v4H0z"/></svg>
      <span>nora@corvelith.ca</span>
    </div>
    <div class="contact-row">
      <svg viewBox="0 0 10 10"><circle cx="5" cy="5" r="4.5"/></svg>
      <span>www.CORVELITH.ca</span>
    </div>
    <div class="file-clerk"><span class="label">File Clerk:</span> Nora Whitcombe</div>
    <div class="practice">
      <div class="label">Practice Restricted</div>
      Serious Personal Injury<br>
      Wrongful Death Litigation<br>
      Long-Term Disability Litigation<br>
      Wrongful Dismissal Litigation<br>
      Employee Terminations
    </div>
  </aside>

  <div class="abs line heading" style="left:53px;top:188px;">Without Prejudice</div>
  <div class="abs line" style="left:53px;top:225px;">March 13, 2024</div>
  <div class="abs line heading" style="left:53px;top:261px;">By Email</div>

  <div class="abs line" style="left:53px;top:316px;">
    Northvale Insurance Company<br>
    Claims Litigation Department<br>
    240 Alder Road North<br>
    P.O. Box 3100<br>
    Fernbrook, ON&nbsp;&nbsp; N4T 7K2
  </div>

  <div class="abs line" style="left:53px;top:426px;">Attention:&nbsp; Mr. Dalton Pryce</div>
  <div class="abs line" style="left:53px;top:463px;">Mr. Pryce:</div>

  <div class="abs line re-label">Re:</div>
  <div class="abs line re-body">
    Harlow v. Benetti et al.<br>
    DOL:&nbsp; September 12, 2019<br>
    Pre-Mediation Settlement Proposal – March 13th, 2024
  </div>
  <div class="abs re-rule"></div>

  <div class="abs" style="left:53px;top:796px;font-size:13px;line-height:17px;">
    Yours very truly,<br>VARENNE PERSONAL INJURY LAWYERS
  </div>

  <div class="abs signature-area" role="img" aria-label="Handwritten signature of Paul D. Varenne"></div>

  <div class="abs" style="left:53px;top:920px;font-size:13px;line-height:21px;">
    Paul D. Varenne<br>
    Varenne Law Professional Corporation<br>
    /nw<br>
    Encl.
  </div>

  <div class="foot-band"></div>
</main>
</body>
</html>
```